First Aid Kit needs packaging design

We're looking for packaging design for our new first aid kit product. We have the logo created for the product. Our brand name is Oakline Haven and our logo will be provided during the design process. We'll also provide photos (have high res files files for final design), and a template design to base off what we're looking for (packaging design template is .ai file). Logo file also attached (.psd & .png). We need to have the first aid kit contents listed on the back of the packaging (similar to the provided packaging template).

Color: We would like to see black, red, and white throughout the design (similar to provided design template)

The final design should communicate urgency, safety, and portability.

Final design should also include a FNSKU barcode (attached)

Below are more details that define the product.

Product Name:
Ultra-Portable & Small 100-Piece First Aid Kit w/ Exclusive Items, Light, Durable Nylon Case, Space Saving Design - A Must Have Survival Kit!

Product Attributes:
BASED ON CUSTOMER FEEDBACK, our newly designed ultra-lightweight and portable kit has been upgraded with BETTER and STRONGER emergency supplies. Stronger scissors and tweezers, more precise compass, sting relief pads, antibacterial ointment and more!
PRODUCED WITH THE HIGHEST QUALITY STANDARDS that only KVB Approved Facilities can meet.
LIGHTWEIGHT, DURABLE & COMPACT. Perfect for an emergency where a oakline haven is necessary to because seconds count!
The ULTIMATE First Aid Kit for Camping, Home, Road Trips, Office, Adventure, School, Workplace, Travel or Sports.

Product Description
Learn How This Ultra-Portable, Light And Rugged First-Aid Kit Can Give You And Your Family The Ultimate Peace Of Mind.
You need to act fast! Quick Action And A Oakline Haven Is Critical In Emergency Situations.

Stay Alert! Our Kit Has Been Redesigned And Bolstered Based On Your Feedback. Weighing Under 1lb. This Is The Lightest First Aid Kit In Its Class! If You Don't Know What To Do, No Problem; We've Included A First Aid Instruction Guide So You Can Administer Aid Correctly.

Take A Look Inside:

Antiseptic cleansing wipes (6 pcs)
Alcohol prep pad (10 pcs)
Butterfly closure strips (6 pcs)
Sterile Gauze Pad (3 pcs)
Extra large adhesive bandage (4 pc)
Adhesive bandages (25 pcs)
Antibacterial Ointment (4 pcs)
Knuckle adhesive bandage (3 pcs)
Fingertip adhesive bandage (3 pcs)
1 disposable cold compress
First aid tape (1 roll)
Cotton tip applicator (10 pcs)
Abdominal pad (1 pc)
Disposable vinyl gloves (2 pc)
Slim rescue howler whistle (1 pc)
Compass (1pc)
Moleskin blister relief (1 pc)
Triangular bandages (1 pc)
Disposable Emergency blanket (1 pc)
1 glow stick
Disposable raincoat (1 pc)
Scissors (1 pc)
PBT conforming bandage 5x3.6cm (1 roll)
CPR facemask (1 pc)
Metal tweezers (1 pc)
Razor Blade (1 pc)
Sewing Kit (1 pc)
Safety Pins (4 pc)
Sting Relief Pads (4 pc)

Let us know if there are any questions around this.

Thank you,

Milo

Target Market(s)

Health Care, First Aid, Sports & Outdoors, automotive safety, office safety

Industry/Entity Type

Health Care

Font styles to use
Sans Serif
Other font styles liked:
• similar to included box design frame/template

Colors
ec1f27
ffffff
000000

Requirements
Must have
• See Project Description
• Color: Black, red, and white
• Barcode: FNSKU Barcode attached
• Design on back needs to show included contents (similar to design template attached)
Nice to have
• See Project Description

```html
<!DOCTYPE html>
<html lang="en">
<head>
<meta charset="utf-8">
<title>Oakline Haven First Aid Kit – Packaging</title>
<link rel="stylesheet" href="https://fonts.googleapis.com/css2?family=Exo+2:wght@600;700;800&family=Open+Sans:wght@700&display=swap">
<style>
  :root {
    --page: #ffffff;
    --panel-light: #fbdcd7;
    --panel-mid: #f6c2bb;
    --panel-edge: #ec9b93;
    --red: #ec1f27;
    --ink: #000000;
    --ink-soft: #1f1f1f;
    --icon-fill: #f3b3ab;
  }
  * { margin: 0; padding: 0; box-sizing: border-box; }
  html, body { width: 1200px; height: 536px; overflow: hidden; background: var(--page); }
  .canvas { position: relative; width: 1200px; height: 536px; }

  .panel {
    position: absolute;
    top: 110px;
    height: 306px;
    border-radius: 26px;
    background:
      radial-gradient(ellipse at 50% 45%, var(--panel-light) 0%, var(--panel-mid) 70%, var(--panel-edge) 100%);
    overflow: hidden;
  }
  .panel--front { left: 110px; width: 450px; }
  .panel--back { left: 692px; width: 452px; }

  .brand {
    position: absolute;
    display: flex; align-items: center; gap: 8px;
    font-family: "Exo 2", sans-serif;
    font-weight: 800;
    color: var(--red);
    white-space: nowrap;
    line-height: 1;
  }
  .brand__dot { border-radius: 50%; background: var(--red); flex: none; }
  .panel--front .brand { left: 50%; top: 150px; transform: translateX(-50%); font-size: 26px; }
  .panel--front .brand__dot { width: 22px; height: 22px; }
  .panel--back .brand { left: 120px; top: 66px; transform: translateX(-50%); font-size: 16px; }
  .panel--back .brand__dot { width: 14px; height: 14px; }

  .product-title {
    position: absolute;
    text-align: center;
    font-family: "Exo 2", sans-serif;
    color: var(--ink);
    line-height: 1;
  }
  .product-title__sub { font-weight: 700; }
  .product-title__main { font-weight: 800; letter-spacing: 0.5px; }
  .product-title__tag { font-weight: 800; }

  .panel--front .product-title { left: 0; right: 0; top: 222px; }
  .panel--front .product-title__sub { font-size: 12px; }
  .panel--front .product-title__main { font-size: 30px; margin-top: 3px; }
  .panel--front .product-title__tag { font-size: 13px; margin-top: 1px; }

  .panel--back .product-title { left: 30px; width: 180px; top: 108px; }
  .panel--back .product-title__sub { font-size: 7.5px; }
  .panel--back .product-title__main { font-size: 18px; margin-top: 2px; }
  .panel--back .product-title__tag { font-size: 8.5px; margin-top: 1px; }

  .item-icons {
    position: absolute; left: 46px; top: 162px;
    display: grid;
    grid-template-columns: repeat(4, 26px);
    grid-auto-rows: 26px;
    column-gap: 12px;
    row-gap: 6px;
  }
  .item-icon {
    border: 1.5px solid var(--ink);
    background: var(--icon-fill);
  }

  .contents {
    position: absolute; left: 242px; top: 16px; width: 186px;
  }
  .contents__heading {
    font-family: "Exo 2", sans-serif;
    font-weight: 700;
    font-size: 15px;
    color: var(--ink-soft);
    text-align: right;
    margin-bottom: 10px;
  }
  .contents__list { list-style: none; }
  .contents__row {
    display: flex; justify-content: space-between;
    font-family: "Open Sans", sans-serif;
    font-weight: 700;
    font-size: 7.2px;
    line-height: 8.6px;
    color: var(--ink-soft);
  }
</style>
</head>
<body>
<main class="canvas">

  <section class="panel panel--front" aria-label="Front of package">
    <div class="brand"><span class="brand__dot"></span>Oakline Haven</div>
    <div class="product-title">
      <p class="product-title__sub">Ultra-Portable &amp; Small 100-Piece</p>
      <p class="product-title__main">First Aid Kit</p>
      <p class="product-title__tag">A Must Have Survival Kit!</p>
    </div>
  </section>

  <section class="panel panel--back" aria-label="Back of package">
    <div class="brand"><span class="brand__dot"></span>Oakline Haven</div>
    <div class="product-title">
      <p class="product-title__sub">Ultra-Portable &amp; Small 100-Piece</p>
      <p class="product-title__main">First Aid Kit</p>
      <p class="product-title__tag">A Must Have Survival Kit!</p>
    </div>

    <div class="item-icons">
      <div class="item-icon" role="img" aria-label="Whistle icon"></div>
      <div class="item-icon" role="img" aria-label="Tape roll icon"></div>
      <div class="item-icon" role="img" aria-label="Emergency blanket icon"></div>
      <div class="item-icon" role="img" aria-label="Compass icon"></div>
      <div class="item-icon" role="img" aria-label="Glow stick icon"></div>
      <div class="item-icon" role="img" aria-label="CPR facemask icon"></div>
      <div class="item-icon" role="img" aria-label="Gloves icon"></div>
      <div class="item-icon" role="img" aria-label="Raincoat icon"></div>
      <div class="item-icon" role="img" aria-label="Safety pin icon"></div>
      <div class="item-icon" role="img" aria-label="Razor blade icon"></div>
      <div class="item-icon" role="img" aria-label="Tweezers icon"></div>
      <div class="item-icon" role="img" aria-label="Bandage roll icon"></div>
      <div class="item-icon" role="img" aria-label="Adhesive bandage icon"></div>
      <div class="item-icon" role="img" aria-label="Cotton tip applicator icon"></div>
      <div class="item-icon" role="img" aria-label="Sewing kit icon"></div>
      <div class="item-icon" role="img" aria-label="Medicine icon"></div>
    </div>

    <div class="contents">
      <h2 class="contents__heading">Take A Look Inside</h2>
      <ul class="contents__list">
        <li class="contents__row"><span>Abdominal pad</span><span>1 pc</span></li>
        <li class="contents__row"><span>Adhesive bandages</span><span>25 pcs</span></li>
        <li class="contents__row"><span>Alcohol prep pad</span><span>10 pcs</span></li>
        <li class="contents__row"><span>Antibacterial Ointment</span><span>4 pcs</span></li>
        <li class="contents__row"><span>Antiseptic cleansing wipes</span><span>6 pcs</span></li>
        <li class="contents__row"><span>Butterfly closure strips</span><span>6 pcs</span></li>
        <li class="contents__row"><span>Compass</span><span>1 pc</span></li>
        <li class="contents__row"><span>Cotton tip applicator</span><span>10 pcs</span></li>
        <li class="contents__row"><span>CPR facemask</span><span>1 pc</span></li>
        <li class="contents__row"><span>Disposable cold compress</span><span>1 pc</span></li>
        <li class="contents__row"><span>Disposable Emergency blanket</span><span>1 pc</span></li>
        <li class="contents__row"><span>Disposable raincoat</span><span>1 pc</span></li>
        <li class="contents__row"><span>Disposable vinyl gloves</span><span>2 pc</span></li>
        <li class="contents__row"><span>Extra large adhesive bandage</span><span>4 pc</span></li>
        <li class="contents__row"><span>Fingertip adhesive bandage</span><span>3 pcs</span></li>
        <li class="contents__row"><span>First aid tape</span><span>1 roll</span></li>
        <li class="contents__row"><span>Glow stick</span><span>1 pc</span></li>
        <li class="contents__row"><span>Knuckle adhesive bandage</span><span>3 pcs</span></li>
        <li class="contents__row"><span>Metal tweezers</span><span>1 pc</span></li>
        <li class="contents__row"><span>Moleskin blister relief</span><span>1 pc</span></li>
        <li class="contents__row"><span>PBT conforming bandage 5x3.6cm</span><span>1 roll</span></li>
        <li class="contents__row"><span>Razor Blade</span><span>1 pc</span></li>
        <li class="contents__row"><span>Safety Pins</span><span>4 pc</span></li>
        <li class="contents__row"><span>Scissors</span><span>1 pc</span></li>
        <li class="contents__row"><span>Sewing Kit</span><span>1 pc</span></li>
        <li class="contents__row"><span>Slim rescue howler whistle</span><span>1 pc</span></li>
        <li class="contents__row"><span>Sterile Gauze Pad</span><span>3 pcs</span></li>
        <li class="contents__row"><span>Sting Relief Pads</span><span>4 pc</span></li>
        <li class="contents__row"><span>Triangular bandages</span><span>1 pc</span></li>
      </ul>
    </div>
  </section>

</main>
</body>
</html>
```